2018 Desk Calendar Design with Better Spine, Better Health with Chiropractic

In conjunction with the Federation of Spinal Wellness Malaysia (FSW), we are organizing a 2018 desk calendar design. The cover page and monthly design size is 210mm (H) x 195mm (W). The will be a total of 27 designs including a cover page (front) [Sample 1], cover page (back) Malaysia National & States Holiday 2018 (https://restdaylist.example.my/2018-dates/) [Sample 2], 12 months design (front) [Sample 3 and 4], 12 months design (back) [Sample 5], Last page (2017 and 2019 calendar) [Sample 6].

Below are some recommendations for monthly back cover design. The main theme remain as Better SPINE, Better HEALTH with CHIROPRACTIC. Each month can in collaborate with of the following element:-

Suggestion 1 (Celebration of the Month)
January - New Year
February - Chinese New Year
March -
April -
May - Labour Day
June - Aidilfitri Festival
July-
August - Independent Day
September - Malaysia Day
October - World Spine Day
November - Deepavali Festival
December - Christmas

Suggestion 2 (States in Malaysia)
January - Perlis
February - Kedah
March - Penang
April - Perak
May - Selangor
June - Negeri Sembilan
July- Melaka
August - Johor
September - Pahang
October - Terengganu
November - Kelantan
December - Sabah & Sarawak

Target Market(s)

Chiropractors and Public

Industry/Entity Type

Chiropractor

Colors

Designer to choose colors to be used in the design.

Requirements
Must have
• The theme for the desk calendar design is Better Spine, Better Health with Chiropractic.
• The cover page should include 5th Anniversary element.
Nice to have
• Lunar or Islamic calendar is optional in the Gregorian calendar.
• AI Format
• Footnote of each page www.spinefsw.example.org

```html
<!DOCTYPE html>
<html lang="en">
<head>
<meta charset="utf-8">
<title>Malaysia National &amp; States Holidays 2018</title>
<link rel="stylesheet" href="https://fonts.googleapis.com/css2?family=Source+Sans+3:wght@300;400;600&display=swap">
<style>
  :root {
    --row-purple: #a7a3d1;
    --row-cream: #fbefb8;
    --ink: #1f1d2b;
    --brand-navy: #2a2f8f;
    --brand-gold: #f2c230;
    --band-deep: #4f7fc4;
    --band-light: #c4d3ec;
    --paper: #ffffff;
  }
  * { margin: 0; padding: 0; box-sizing: border-box; }
  html, body { width: 1117px; height: 1200px; overflow: hidden; background: var(--paper); }
  body { font-family: "Source Sans 3", "Myriad Pro", sans-serif; color: var(--ink); position: relative; }
  .page-title {
    position: absolute; top: 48px; left: 0; width: 1117px;
    text-align: center; font-size: 22px; font-weight: 400;
  }
  .holiday-table {
    position: absolute; top: 79px; left: 29px; width: 1052px;
    border-collapse: collapse; table-layout: fixed; font-size: 15px; font-weight: 300; line-height: 1;
  }
  .holiday-table th, .holiday-table td {
    height: 19.4px; padding: 0; text-align: left; font-weight: 300; white-space: nowrap; vertical-align: middle;
  }
  .holiday-table tr:nth-child(odd) { background: var(--row-purple); }
  .holiday-table tr:nth-child(even) { background: var(--row-cream); }
  .col-date { width: 94px; padding-left: 21px !important; }
  .col-day { width: 72px; }
  .col-holiday { width: 363px; }
  .footer-band { position: absolute; left: 330px; top: 1045px; width: 787px; height: 155px; }
  .brand-mark {
    position: absolute; left: 30px; top: 1092px; display: flex; align-items: center; gap: 8px;
  }
  .brand-mark .dot { width: 46px; height: 46px; border-radius: 50%; background: var(--brand-gold); }
  .brand-mark .name { font-size: 26px; font-weight: 600; color: var(--brand-navy); }
  .anniversary-emblem {
    position: absolute; left: 158px; top: 1058px; width: 156px; height: 122px;
    border-radius: 50%;
    background: radial-gradient(circle at 50% 45%, #f4e4a6 0%, #d3d4ee 62%, rgba(255,255,255,0) 72%);
  }
  .site-url {
    position: absolute; right: 14px; top: 1163px; font-size: 21px; font-weight: 400; color: var(--ink);
  }
</style>
</head>
<body>
  <h1 class="page-title">Malaysia National &amp; States Holidays 2018</h1>

  <table class="holiday-table">
    <colgroup><col class="col-date"><col class="col-day"><col class="col-holiday"><col></colgroup>
    <tr><th class="col-date">Date</th><th>Day</th><th>Holiday</th><th>States</th></tr>
    <tr><td class="col-date">1 Jan</td><td>Mon</td><td>New Year's Day</td><td>National except Johor, Kedah, Kelantan, Perlis &amp; Terengganu</td></tr>
    <tr><td class="col-date">14 Jan</td><td>Sun</td><td>YDPB Negeri Sembilan's Birthday</td><td>Negeri Sembilan</td></tr>
    <tr><td class="col-date">21 Jan</td><td>Sun</td><td>Sultan of Kedah's Birthday</td><td>Kedah</td></tr>
    <tr><td class="col-date">31 Jan</td><td>Wed</td><td>Thaipusam</td><td>Johor, Kuala Lumpur, Negeri Sembilan, Penang, Perak, Putrajaya &amp; Selangor</td></tr>
    <tr><td class="col-date">1 Feb</td><td>Thu</td><td>Federal Territory Day</td><td>Kuala Lumpur, Labuan &amp; Putrajaya</td></tr>
    <tr><td class="col-date">16 Feb</td><td>Fri</td><td>Chinese New Year</td><td>National</td></tr>
    <tr><td class="col-date">17 Feb</td><td>Sat</td><td>Chinese New Year Holiday</td><td>National</td></tr>
    <tr><td class="col-date">18 Feb</td><td>Sun</td><td>Chinese New Year Holiday</td><td>Johor, Kedah, Kelantan &amp; Terengganu</td></tr>
    <tr><td class="col-date">4 Mar</td><td>Sun</td><td>Installation of Sultan Terengganu</td><td>Terengganu</td></tr>
    <tr><td class="col-date">23 Mar</td><td>Fri</td><td>Sultan of Johor's Birthday</td><td>Johor</td></tr>
    <tr><td class="col-date">30 Mar</td><td>Fri</td><td>Good Friday</td><td>Sabah &amp; Sarawak</td></tr>
    <tr><td class="col-date">14 Apr</td><td>Sat</td><td>Israk and Mikraj</td><td>Kedah, Negeri Sembilan &amp; Perlis</td></tr>
    <tr><td class="col-date">15 Apr</td><td>Sun</td><td>Declaration of Melaka as a Historical City</td><td>Melaka</td></tr>
    <tr><td class="col-date">26 Apr</td><td>Thu</td><td>Sultan of Terengganu's Birthday</td><td>Terengganu</td></tr>
    <tr><td class="col-date">1 May</td><td>Tue</td><td>Labour Day</td><td>National</td></tr>
    <tr><td class="col-date">7 May</td><td>Mon</td><td>Hari Hol Pahang</td><td>Pahang</td></tr>
    <tr><td class="col-date">17 May</td><td>Thu</td><td>Awal Ramadan</td><td>Johor, Kedah &amp; Melaka</td></tr>
    <tr><td class="col-date">17 May</td><td>Thu</td><td>Raja Perlis' Birthday</td><td>Perlis</td></tr>
    <tr><td class="col-date">29 May</td><td>Tue</td><td>Wesak Day</td><td>National</td></tr>
    <tr><td class="col-date">30 May</td><td>Wed</td><td>Harvest Festival</td><td>Labuan &amp; Sabah</td></tr>
    <tr><td class="col-date">31 May</td><td>Thu</td><td>Harvest Festival Holiday</td><td>Labuan &amp; Sabah</td></tr>
    <tr><td class="col-date">1 Jun</td><td>Fri</td><td>Hari Gawai</td><td>Sarawak</td></tr>
    <tr><td class="col-date">2 Jun</td><td>Sat</td><td>Hari Gawai Holiday</td><td>Sarawak</td></tr>
    <tr><td class="col-date">2 Jun</td><td>Sat</td><td>Nuzul Al-Quran</td><td>National except Johor, Kedah, Melaka, Negeri Sembilan, Sabah &amp; Sarawak</td></tr>
    <tr><td class="col-date">15 Jun</td><td>Fri</td><td>Hari Raya Aidilfitri</td><td>National</td></tr>
    <tr><td class="col-date">16 Jun</td><td>Sat</td><td>Hari Raya Aidilfitri Holiday</td><td>National</td></tr>
    <tr><td class="col-date">17 Jun</td><td>Sun</td><td>Hari Raya Aidilfitri Holiday</td><td>Johor, Kedah, Kelantan &amp; Terengganu</td></tr>
    <tr><td class="col-date">7 Jul</td><td>Sat</td><td>Georgetown World Heritage City Day</td><td>Penang</td></tr>
    <tr><td class="col-date">14 Jul</td><td>Sat</td><td>Penang Governor's Birthday</td><td>Penang</td></tr>
    <tr><td class="col-date">22 Jul</td><td>Sun</td><td>Sarawak Day</td><td>Sarawak</td></tr>
    <tr><td class="col-date">22 Aug</td><td>Wed</td><td>Hari Raya Haji</td><td>National</td></tr>
    <tr><td class="col-date">23 Aug</td><td>Thu</td><td>Hari Raya Haji Holiday</td><td>Kedah, Kelantan, Perlis &amp; Terengganu</td></tr>
    <tr><td class="col-date">31 Aug</td><td>Fri</td><td>Merdeka Day</td><td>National</td></tr>
    <tr><td class="col-date">9 Sep</td><td>Sun</td><td>Agong's Birthday</td><td>National</td></tr>
    <tr><td class="col-date">9 Sep</td><td>Sun</td><td>Sarawak Governor's Birthday</td><td>Sarawak</td></tr>
    <tr><td class="col-date">11 Sep</td><td>Tue</td><td>Awal Muharram</td><td>National</td></tr>
    <tr><td class="col-date">16 Sep</td><td>Sun</td><td>Malaysia Day</td><td>National</td></tr>
    <tr><td class="col-date">17 Sep</td><td>Mon</td><td>Malaysia Day Holiday</td><td>National except Johor, Kedah, Kelantan &amp; Terengganu</td></tr>
    <tr><td class="col-date">6 Oct</td><td>Sat</td><td>Sabah Governor's Birthday</td><td>Sabah</td></tr>
    <tr><td class="col-date">12 Oct</td><td>Fri</td><td>Melaka Governor's Birthday</td><td>Melaka</td></tr>
    <tr><td class="col-date">15 Oct</td><td>Mon</td><td>Hari Hol Almarhum Sultan Iskandar</td><td>Johor</td></tr>
    <tr><td class="col-date">24 Oct</td><td>Wed</td><td>Sultan of Pahang's Birthday</td><td>Pahang</td></tr>
    <tr><td class="col-date">2 Nov</td><td>Fri</td><td>Sultan of Perak's Birthday</td><td>Perak</td></tr>
    <tr><td class="col-date">6 Nov</td><td>Tue</td><td>Deepavali</td><td>National except Sarawak</td></tr>
    <tr><td class="col-date">11 Nov</td><td>Sun</td><td>Sultan of Kelantan's Birthday</td><td>Kelantan</td></tr>
    <tr><td class="col-date">12 Nov</td><td>Mon</td><td>Sultan of Kelantan's Birthday Holiday</td><td>Kelantan</td></tr>
    <tr><td class="col-date">20 Nov</td><td>Tue</td><td>Prophet Muhammad's Birthday</td><td>National</td></tr>
    <tr><td class="col-date">11 Dec</td><td>Tue</td><td>Sultan of Selangor's Birthday</td><td>Selangor</td></tr>
    <tr><td class="col-date">25 Dec</td><td>Tue</td><td>Christmas Day</td><td>National</td></tr>
  </table>

  <svg class="footer-band" viewBox="0 0 787 155" role="img" aria-label="Decorative blue footer band">
    <defs>
      <linearGradient id="bandFill" x1="0" y1="1" x2="1" y2="0">
        <stop offset="0" stop-color="var(--band-light)"/>
        <stop offset="1" stop-color="var(--band-deep)"/>
      </linearGradient>
    </defs>
    <path d="M0 155 C 260 90, 520 50, 787 0 L787 155 Z" fill="url(#bandFill)" opacity="0.8"/>
  </svg>

  <div class="brand-mark">
    <span class="dot"></span>
    <span class="name">FSW</span>
  </div>
  <div class="anniversary-emblem" role="img" aria-label="Fifth anniversary emblem"></div>

  <div class="site-url">www.spinefsw.example.org</div>
</body>
</html>
```